Business card design for holistic health care clinic

We need a double-sided business card design for our holistic health care clinic that integrates our logo design and also its color scheme. My business is called Valmira. It is an integrative medicine clinic. You have already done the logo for me. Please ensure an elegant and upscale design that is not cluttered, but still has all the necessary information (please see below for details).

Target Market(s)

Wellness, fitness, rehabilitation for educated, well-traveled open-minded clients who are focused on natural, organic, balanced and preventive healthcare and lifestyle.

Industry/Entity Type

Medical

Contact Information for Business Card

Modern, clean.

Number of Pages Required

1 page

Font styles to use
Serif
Sans Serif

Colors

Designer to choose colors to be used in the design.

Requirements
Must have
• Logo on one side, all other information on the other side.
• Other information should include:
• Tobias Wrenfeld - DOE, CPT, LMT
• 4100 East Marrow Drive
• Austin, TX 78119
• 512 555 0148
• 818 555 0192
• info@ValmiraHealth.example
• t.wrenfeld@ValmiraHealth.example
Nice to have
• Darker background on front - but not totally black - shaded/dark gray.

```html
<!DOCTYPE html>
<html lang="en">
<head>
<meta charset="utf-8">
<title>Valmira – Business Card</title>
<link rel="stylesheet" href="https://fonts.googleapis.com/css2?family=Source+Sans+3:ital,wght@0,400;0,600;0,700;1,400&display=swap">
<style>
  :root {
    --backdrop: #3a322e;
    --card: #17181a;
    --card-edge: #222326;
    --brand-blue: #1f8fd3;
    --ink-light: #e9ecef;
    --divider: #6b6f75;
  }
  * { box-sizing: border-box; margin: 0; padding: 0; }
  html, body {
    width: 1200px; height: 864px; overflow: hidden;
    background: var(--backdrop);
    font-family: "Source Sans 3", "Helvetica Neue", Arial, sans-serif;
  }
  .stage { position: relative; width: 1200px; height: 864px; }
  .card {
    position: absolute; width: 560px; height: 320px;
    background: linear-gradient(145deg, var(--card-edge), var(--card));
    border-radius: 6px;
    box-shadow: 0 14px 30px rgba(0,0,0,.45);
    overflow: hidden;
  }
  /* Front side */
  .card-front { left: 50px; top: 90px; }
  .card-front .tagline {
    position: absolute; top: 44px; left: 0; right: 0; text-align: center;
    color: var(--brand-blue); font-style: italic; font-size: 15px;
  }
  .card-front .brand-mark {
    position: absolute; top: 0; left: 0; right: 0; bottom: 0;
    display: flex; align-items: center; justify-content: center; gap: 18px;
  }
  .card-front .brand-dot {
    width: 34px; height: 34px; border-radius: 50%; background: var(--brand-blue);
  }
  .card-front .brand-name {
    color: var(--brand-blue); font-weight: 700; font-size: 72px;
    letter-spacing: 2px; text-transform: uppercase;
  }
  /* Back side */
  .card-back { left: 590px; top: 450px; }
  .brand-block {
    position: absolute; left: 34px; top: 112px; width: 230px;
  }
  .brand-block .brand-name {
    color: var(--brand-blue); font-weight: 700; font-size: 50px;
    letter-spacing: 1px; text-transform: uppercase; line-height: 1;
  }
  .brand-block .brand-sub {
    color: var(--brand-blue); font-size: 15px; margin-top: 6px; white-space: nowrap;
  }
  .divider {
    position: absolute; left: 272px; top: 50px; width: 1px; height: 220px;
    background: linear-gradient(to bottom, transparent, var(--divider), transparent);
  }
  .contact {
    position: absolute; left: 290px; top: 66px; right: 14px;
    color: var(--ink-light); font-size: 14.5px; line-height: 1.32;
  }
  .contact .person {
    color: var(--brand-blue); font-weight: 700; font-size: 17px; text-transform: uppercase;
    margin-bottom: 6px; white-space: nowrap;
  }
  .contact .person .credentials { font-size: 11px; font-weight: 600; }
  .contact .address { margin-bottom: 4px; }
  .contact ul { list-style: none; }
  .contact li { display: flex; align-items: center; gap: 8px; white-space: nowrap; }
  .contact li svg { width: 12px; height: 12px; flex: none; fill: var(--brand-blue); }
</style>
</head>
<body>
<main class="stage">
  <section class="card card-front" aria-label="Card front">
    <p class="tagline">helping the body help itself</p>
    <div class="brand-mark">
      <span class="brand-dot"></span>
      <span class="brand-name">Valmira</span>
    </div>
  </section>

  <section class="card card-back" aria-label="Card back">
    <div class="brand-block">
      <div class="brand-name">Valmira</div>
      <div class="brand-sub">Integrative Holistic Medicine</div>
    </div>
    <div class="divider"></div>
    <div class="contact">
      <p class="person">Tobias Wrenfeld <span class="credentials">- DOE, CPT, LMT</span></p>
      <p class="address">4100 East Marrow Drive<br>Austin, TX 78119</p>
      <ul>
        <li><svg viewBox="0 0 24 24"><path d="M6.6 10.8a15 15 0 0 0 6.6 6.6l2.2-2.2a1 1 0 0 1 1-.25 11.4 11.4 0 0 0 3.6.57 1 1 0 0 1 1 1V20a1 1 0 0 1-1 1A17 17 0 0 1 3 4a1 1 0 0 1 1-1h3.5a1 1 0 0 1 1 1c0 1.25.2 2.45.57 3.57a1 1 0 0 1-.25 1z"/></svg>512 555 0148</li>
        <li><svg viewBox="0 0 24 24"><path d="M7 1h10a2 2 0 0 1 2 2v18a2 2 0 0 1-2 2H7a2 2 0 0 1-2-2V3a2 2 0 0 1 2-2zm0 3v14h10V4zm5 15.5a1 1 0 1 0 0 2 1 1 0 0 0 0-2z"/></svg>818 555 0192</li>
        <li><svg viewBox="0 0 24 24"><path d="M2 5h20v14H2zm2 2v.5l8 5 8-5V7zm0 3v7h16v-7l-8 5z"/></svg>t.wrenfeld@ValmiraHealth.example</li>
        <li><svg viewBox="0 0 24 24"><path d="M2 5h20v14H2zm2 2v.5l8 5 8-5V7zm0 3v7h16v-7l-8 5z"/></svg>info@ValmiraHealth.example</li>
        <li><svg viewBox="0 0 24 24"><path d="M12 2a10 10 0 1 0 0 20 10 10 0 0 0 0-20zm-1 17.9A8 8 0 0 1 4.2 10l4.8 4.8v1a2 2 0 0 0 2 2zm6.9-2.5A2 2 0 0 0 16 16h-1v-3a1 1 0 0 0-1-1H8v-2h2a1 1 0 0 0 1-1V7h2a2 2 0 0 0 2-2v-.4a8 8 0 0 1 2.9 12.8z"/></svg>www.ValmiraHealth.example</li>
      </ul>
    </div>
  </section>
</main>
</body>
</html>
```